Bluecrest Learning Corps by graduating students from college in two years

Based on the logo design, create stationary and business cards for
Dr. Venrel T Oskamp, CEO, (703) 482-1736
and Marisa Deltoft, Respresentative, (301) 647-2208
Address: 4719 Pellham Court, Dunmere Station, VA 22418
Incorporate elelments of the logo

Target Market(s)

USA

Font styles to use
Other font styles liked:
• match with the logo type style

```html
<!DOCTYPE html>
<html lang="en">
<head>
<meta charset="utf-8">
<title>Bluecrest Learning Corps – Letterhead</title>
<link rel="stylesheet" href="https://fonts.googleapis.com/css2?family=Lato:wght@400;700&family=Open+Sans:wght@400;600;700&display=swap">
<style>
  :root {
    --navy: #0b1f5c;
    --gold: #f2bf2e;
    --paper: #f8f8f8;
    --backdrop: #e6e6e6;
    --ink: #111111;
    --body-text: #6b6b6b;
    --muted: #777777;
  }
  * { margin: 0; padding: 0; box-sizing: border-box; }
  html, body { width: 1200px; height: 1200px; overflow: hidden; background: var(--backdrop); }
  .letterhead {
    position: absolute; left: 205px; top: 36px;
    width: 790px; height: 1128px;
    background: var(--paper);
    overflow: hidden;
    font-family: "Lato", sans-serif;
  }
  .header-waves { position: absolute; left: 0; top: 0; width: 790px; height: 200px; }
  .brand-seal {
    position: absolute; left: 58px; top: 37px;
    width: 176px; height: 176px; border-radius: 50%;
    background: #ffffff;
    display: flex; align-items: center; justify-content: center;
    text-align: center;
  }
  .brand-name {
    font-family: "Open Sans", sans-serif; font-weight: 700;
    font-size: 17px; line-height: 1.25; color: var(--navy);
    width: 130px;
  }
  .contact-block {
    position: absolute; left: 504px; top: 58px; height: 137px;
    border-left: 2px solid var(--navy);
    padding-left: 11px;
    font-family: "Open Sans", sans-serif; font-style: normal; color: var(--ink);
    font-size: 13px; line-height: 19.5px;
  }
  .contact-name { font-weight: 700; color: var(--navy); font-size: 14.5px; }
  .contact-name + .contact-phone + .contact-name { margin-top: 2px; }
  .contact-phone { display: flex; align-items: center; gap: 4px; }
  .contact-phone svg { width: 12px; height: 12px; fill: var(--navy); }
  .contact-label { font-weight: 600; color: var(--navy); font-size: 13.5px; margin-top: 6px; }
  .recipient { position: absolute; left: 75px; top: 320px; }
  .recipient-name { font-size: 15.5px; font-weight: 700; color: var(--ink); }
  .recipient-title { font-size: 11px; font-weight: 700; color: var(--ink); margin-top: 2px; }
  .letter-date { position: absolute; right: 75px; top: 341px; font-size: 11.5px; color: var(--muted); }
  .letter-body { position: absolute; left: 75px; top: 396px; width: 640px; }
  .letter-body p {
    font-size: 11.4px; line-height: 18.7px; color: var(--body-text);
    text-align: justify; margin-bottom: 18.7px; hyphens: auto;
  }
  .signature-mark {
    position: absolute; left: 75px; top: 832px; width: 165px; height: 40px;
    background: linear-gradient(90deg, rgba(20,20,20,0.10), rgba(20,20,20,0.03));
    border-radius: 4px;
  }
  .signer { position: absolute; left: 75px; top: 895px; }
  .signer-name { font-size: 15.5px; font-weight: 700; color: var(--ink); }
  .signer-title { font-size: 11.5px; font-weight: 700; color: var(--muted); margin-top: 3px; }
</style>
</head>
<body>
  <main class="letterhead">
    <svg class="header-waves" viewBox="0 0 790 200" aria-hidden="true">
      <path fill="#0b1f5c" d="M0 0 H790 V20 C600 16 420 34 300 58 C180 82 80 118 0 150 Z"/>
      <path fill="#f2bf2e" d="M0 122 C150 70 400 30 790 25 V42 C560 40 360 58 230 84 C140 102 60 126 0 142 Z"/>
      <path fill="#0b1f5c" d="M0 146 C70 124 150 102 230 88 C150 108 70 134 0 160 Z"/>
      <path fill="#f2bf2e" d="M420 48 C500 34 600 24 720 20 C600 28 500 40 420 52 Z"/>
    </svg>

    <div class="brand-seal">
      <span class="brand-name">Bluecrest Learning Corps</span>
    </div>

    <address class="contact-block">
      <div class="contact-name">Dr. Venrel T Oskamp, CEO</div>
      <div class="contact-phone"><svg viewBox="0 0 24 24"><path d="M6.6 10.8a15 15 0 0 0 6.6 6.6l2.2-2.2a1 1 0 0 1 1-.25 11.4 11.4 0 0 0 3.6.57 1 1 0 0 1 1 1V20a1 1 0 0 1-1 1A17 17 0 0 1 3 4a1 1 0 0 1 1-1h3.5a1 1 0 0 1 1 1c0 1.25.2 2.45.57 3.57a1 1 0 0 1-.25 1z"/></svg>(703) 482-1736</div>
      <div class="contact-name">Marisa Deltoft, Respresentative</div>
      <div class="contact-phone"><svg viewBox="0 0 24 24"><path d="M6.6 10.8a15 15 0 0 0 6.6 6.6l2.2-2.2a1 1 0 0 1 1-.25 11.4 11.4 0 0 0 3.6.57 1 1 0 0 1 1 1V20a1 1 0 0 1-1 1A17 17 0 0 1 3 4a1 1 0 0 1 1-1h3.5a1 1 0 0 1 1 1c0 1.25.2 2.45.57 3.57a1 1 0 0 1-.25 1z"/></svg>(301) 647-2208</div>
      <div class="contact-label">Address:</div>
      <div>4719 Pellham Court</div>
      <div>Dunmere Station, VA 22418</div>
    </address>

    <div class="recipient">
      <div class="recipient-name">Dear. Mrs Lorna Vance Hadley</div>
      <div class="recipient-title">Chief Director</div>
    </div>
    <div class="letter-date">Date: 24-february-2025</div>

    <section class="letter-body">
      <p>Lorem ipsum dolor sit amet, consectetur adipiscing elit, sed do eiusmod tempor incididunt ut labore et dolore magna aliqua. Sollicitudin ac orci phasellus egestas tellus rutrum tellus. Euismod elementum nisi quis eleifend quam adipiscing vitae proin sagittis. Egestas sed tempus urna et pharetra pharetra. Quis blandit turpis cursus in hac habitasse. Sed velit dignissim sodales ut eu. Ac auctor augue mauris augue neque. In arcu cursus euismod quis viverra nibh cras pulvinar mattis. Libero justo laoreet sit amet. Felis eget nunc lobortis mattis aliquam faucibus purus in. Pulvinar etiam non quam lacus suspendisse faucibus. Odio tempor orci dapibus ultrices. Velit dignissim sodales ut eu sem integer vitae justo. Fermentum et sollicitudin ac orci phasellus egestas. Pharetra vel turpis nunc eget lorem dolor sed. Sed turpis tincidunt id aliquet risus feugiat in ante. Mus mauris vitae ultricies leo integer malesuada nunc vel. Rhoncus urna neque viverra justo nec ultrices dui. Ut placerat orci nulla pellentesque dignissim enim sit amet.</p>
      <p>Bibendum arcu vitae elementum curabitur vitae nunc. Nunc pulvinar sapien et ligula ullamcorper malesuada. At elementum eu facilisis sed. Erat pellentesque adipiscing commodo elit at imperdiet dui accumsan sit. Nunc scelerisque viverra mauris in aliquam sem fringilla. In vitae turpis massa sed. Volutpat ac tincidunt vitae semper quis lectus nulla at. Massa placerat duis ultricies lacus sed turpis. Dui vivamus arcu felis bibendum ut tristique et egestas. Blandit aliquam etiam erat velit scelerisque in dictum non consectetur. Id neque aliquam vestibulum morbi blandit cursus risus at. Sed egestas egestas fringilla phasellus faucibus scelerisque eleifend donec. Ornare quam viverra orci sagittis eu volutpat odio facilisis. Volutpat sed cras ornare arcu dui vivamus arcu. Interdum consectetur libero id faucibus nisl.</p>
      <p>Viverra mauris in aliquam sem. Mattis molestie a iaculis at erat pellentesque adipiscing commodo elit. Sit amet volutpat consequat mauris nunc. Aliquam nulla facilisi cras fermentum. Sed turpis tincidunt id aliquet risus feugiat. Augue neque gravida in fermentum et sollicitudin ac orci.</p>
    </section>

    <div class="signature-mark" role="img" aria-label="Handwritten signature of the sender"></div>
    <div class="signer">
      <div class="signer-name">Tomas Everly Brandt</div>
      <div class="signer-title">Chief Director</div>
    </div>
  </main>
</body>
</html>
```